velorahelp Web Design Project

It is a virtual assistance/concierge company that helps the busy professional by remotely providing administrative, technical and/or creative business support services, specializing in the medical device industry. Company name is velorahelp.
(website will be velorahelp.example)

Allowing things to be done without taking time away from more urgent issues or family/personal time. Partnering with a VA reduces stress, protects cash flow, eliminates administrative hassles, and enables business people to find the success they originally set out to achieve. Saves small businesses and/or individuals on overhead, salary, et. Work is done remotely to offer administrative, clerical, typing and specialist service assistance on a regular, ad-hoc or emergency cover basis.

Though we are capable of addressing the needs of medical professionals and industry representatives due to our experience and knowledge (sales, HCC guidelines, etc.) we do not want to be limited to that market only.

Target Market(s)

Target market would be M/F, 30-50, National, busy, Alpha, entrepreneurs and industry professionals who want/need to do more without sacrifice of life

Requirements
Nice to have
• We do have a logo designed via the PlanMarket website that can/should be included. Logo is uploaded.

```html
<!DOCTYPE html>
<html lang="en">
<head>
<meta charset="utf-8">
<title>velorahelp – Virtual Assistance</title>
<link rel="stylesheet" href="https://fonts.googleapis.com/css2?family=Noto+Sans:wght@400;700&family=Tinos:ital,wght@1,400;1,700&display=swap">
<style>
  :root {
    --ink: #2b2b2b;
    --muted: #6b6b6b;
    --brand-red: #c8202b;
    --brand-navy: #1f3a78;
    --accent: #2a78c2;
    --line: #c9c9c9;
    --footer-bg: #f8f8f8;
  }
  * { box-sizing: border-box; margin: 0; padding: 0; }
  html, body { width: 722px; height: 1200px; overflow: hidden; background: #fff; }
  body { position: relative; font-family: "Noto Sans", Verdana, sans-serif; color: var(--ink); }
  .abs { position: absolute; }

  /* header */
  .brand { left: 73px; top: 32px; display: flex; align-items: center; gap: 6px; }
  .brand-dot { width: 15px; height: 15px; border-radius: 50%; background: var(--brand-red); }
  .brand-name { font-size: 28px; font-weight: 700; color: var(--brand-navy); letter-spacing: -0.5px; line-height: 1; }
  .call-line { right: 70px; top: 27px; font-size: 12px; color: var(--muted); }
  .search { left: 518px; top: 52px; width: 134px; height: 23px; border: 1px solid var(--line); border-radius: 3px; font-size: 11px; color: var(--muted); padding: 4px 6px; }
  .search svg { position: absolute; right: 6px; top: 5px; }

  /* navigation */
  .main-nav { left: 72px; top: 93px; width: 581px; height: 47px; border: 1px solid var(--line); border-radius: 5px; font-size: 12.5px; color: var(--ink); }
  .main-nav span { position: absolute; top: 15px; }
  .main-nav .current { text-decoration: underline; }

  /* hero */
  .hero { left: 73px; top: 152px; width: 579px; height: 242px;
    background: linear-gradient(90deg, #d4d6d9 0%, #eef0f2 12%, #7aa7d6 21%, #f1f1f0 30%, #e9d3c4 40%, #8fb5db 50%, #f6f6f6 58%, #e8d2bf 67%, #fbfbfb 74%, #9ab4cf 80%, #a9aaac 90%, #d9dadc 100%);
    box-shadow: 0 2px 5px rgba(0,0,0,.35); }
  .slider-dots { left: 345px; top: 406px; display: flex; gap: 3px; }
  .slider-dots i { width: 8px; height: 8px; border-radius: 50%; background: #8d8d8d; display: block; }
  .slider-dots i.on { background: var(--accent); }

  /* feature columns */
  .feature { width: 182px; }
  .feature h3 { font-family: "Tinos", "Times New Roman", serif; font-style: italic; font-weight: 700; font-size: 13px; text-align: center; margin-bottom: 16px; }
  .feature .photo { width: 180px; height: 105px; box-shadow: 0 1px 3px rgba(0,0,0,.4); }
  .feature p { font-size: 11.5px; line-height: 16px; margin-top: 17px; padding-left: 1px; }

  .btn-more { display: block; width: 50px; height: 25px; border: 1px solid var(--line); border-radius: 5px; background: linear-gradient(#fff, #ececec); font-size: 11px; color: var(--accent); text-align: center; line-height: 23px; box-shadow: 1px 1px 1px rgba(0,0,0,.15); }

  /* welcome & services */
  .section-title { font-family: "Tinos", "Times New Roman", serif; font-style: italic; font-weight: 400; font-size: 14px; color: var(--ink); }
  .section-title b { color: var(--accent); font-weight: 700; }
  .welcome-text { left: 76px; top: 764px; width: 360px; font-size: 11.5px; line-height: 20px; }
  .service-list { left: 465px; top: 760px; list-style: none; font-size: 11.5px; }
  .service-list li { display: flex; align-items: center; gap: 8px; height: 24.4px; }

  /* clients */
  .clients { left: 74px; top: 958px; width: 579px; height: 157px; border: 1px solid #d8d8d8; border-radius: 5px; box-shadow: 0 1px 4px rgba(0,0,0,.2); }
  .clients .rule { position: absolute; left: 10px; right: 14px; top: 31px; border-top: 1px solid var(--line); }
  .client { position: absolute; top: 42px; width: 125px; }
  .client .photo { height: 74px; border: 1px solid #aaa;
    background: linear-gradient(90deg, #8c9a7a 0%, #c9a48c 22%, #e7c2a8 45%, #d9b097 62%, #b9c6c2 80%, #9fae98 100%); }
  .client span { display: block; margin-top: 12px; font-family: "Tinos", "Times New Roman", serif; font-style: italic; font-size: 10.5px; padding-left: 3px; }
  .pager { position: absolute; top: 9px; }

  /* footer */
  .site-footer { left: 0; top: 1133px; width: 722px; height: 67px; background: var(--footer-bg); border-top: 1px solid #dedede; }
  .footer-contact { position: absolute; left: 77px; top: 8px; font-size: 8.5px; line-height: 10px; color: var(--muted); }
  .footer-contact strong { font-size: 12px; font-style: italic; text-decoration: underline; color: #777; display: block; line-height: 14px; margin-bottom: 1px; }
  .find-us { position: absolute; left: 530px; top: 19px; font-size: 8.5px; color: var(--muted); display: flex; align-items: center; gap: 6px; }
  .find-us i { display: block; width: 12px; height: 12px; border-radius: 2px; background: #4a78b0; }
  .legal { position: absolute; left: 515px; top: 38px; font-size: 8.5px; color: var(--muted); }
</style>
</head>
<body>

<header>
  <div class="abs brand"><span class="brand-dot"></span><span class="brand-name">velorahelp</span></div>
  <div class="abs call-line">Call us @ 1800 - 55 - 730418</div>
  <div class="abs search">search...
    <svg width="12" height="12" viewBox="0 0 12 12"><circle cx="5" cy="5" r="3.5" fill="none" stroke="#888" stroke-width="1.5"/><line x1="7.6" y1="7.6" x2="11" y2="11" stroke="#888" stroke-width="2"/></svg>
  </div>
</header>

<nav class="abs main-nav">
  <span class="current" style="left:30px">Home</span>
  <span style="left:110px">|</span>
  <span style="left:158px">About Us</span>
  <span style="left:262px">|</span>
  <span style="left:310px">Our Services</span>
  <span style="left:437px">|</span>
  <span style="left:481px">Contact Us</span>
</nav>

<div class="abs hero" role="img" aria-label="Doctor with stethoscope in front of medical staff attending a patient in a bright clinic"></div>
<div class="abs slider-dots"><i class="on"></i><i></i><i></i><i></i></div>

<section class="abs feature" style="left:74px;top:451px">
  <h3>Recieving calls</h3>
  <div class="photo" role="img" aria-label="Call centre agent with headset in an office" style="background:linear-gradient(90deg,#8a7a4a 0%,#c9b27a 25%,#e9dcc0 45%,#b98a6e 62%,#f0e6d8 80%,#f7f3ea 100%)"></div>
  <p>Put here something about collection of client query or calls to researching over them in a brief.</p>
</section>
<section class="abs feature" style="left:272px;top:451px">
  <h3>Reserching Issues</h3>
  <div class="photo" role="img" aria-label="Man at a desk with computer monitors" style="background:linear-gradient(90deg,#4e5a4c 0%,#8fb0c8 18%,#c9d7e2 38%,#5f7a55 50%,#d8b49a 68%,#8aa0c2 85%,#cfcac0 100%)"></div>
  <p>Put here something about researching of client query or calls to researching over them in a brief.</p>
</section>
<section class="abs feature" style="left:471px;top:451px">
  <h3>Resolving Problems</h3>
  <div class="photo" role="img" aria-label="Business handshake" style="background:linear-gradient(90deg,#1f2736 0%,#3a4658 20%,#9a6e52 40%,#c99a7c 55%,#2a3344 72%,#a9c9e6 88%,#cfe1f0 100%)"></div>
  <p>Put here something about resolving of client query or calls to researching over them in a brief.</p>
</section>
<a class="abs btn-more" style="left:75px;top:680px">More</a>
<a class="abs btn-more" style="left:273px;top:680px">More</a>
<a class="abs btn-more" style="left:471px;top:680px">More</a>

<h2 class="abs section-title" style="left:75px;top:737px"><b>Welcome</b> to our site</h2>
<p class="abs welcome-text">It is a virtual assistance/concierge company that helps the busy professional by remotely providing administrative, technical and/or creative business support services, specializing in the medical device industry. Company name is velorahelp. It is a virtual assistance/concierge company that helps the busy professional by remotely providing administrative, technical and/or creative business support services.</p>
<a class="abs btn-more" style="left:75px;top:917px">More</a>

<h2 class="abs section-title" style="left:465px;top:737px"><b>Our</b> Services</h2>
<ul class="abs service-list">
  <li><svg width="17" height="17" viewBox="0 0 17 17"><circle cx="8.5" cy="8.5" r="7.5" fill="#f2f2f2" stroke="#bbb"/><path d="M7 5.5 L11 8.5 L7 11.5Z" fill="#3a8fc4"/></svg>Service goes here</li>
  <li><svg width="17" height="17" viewBox="0 0 17 17"><circle cx="8.5" cy="8.5" r="7.5" fill="#f2f2f2" stroke="#bbb"/><path d="M7 5.5 L11 8.5 L7 11.5Z" fill="#3a8fc4"/></svg>Service goes here</li>
  <li><svg width="17" height="17" viewBox="0 0 17 17"><circle cx="8.5" cy="8.5" r="7.5" fill="#f2f2f2" stroke="#bbb"/><path d="M7 5.5 L11 8.5 L7 11.5Z" fill="#3a8fc4"/></svg>Service goes here</li>
  <li><svg width="17" height="17" viewBox="0 0 17 17"><circle cx="8.5" cy="8.5" r="7.5" fill="#f2f2f2" stroke="#bbb"/><path d="M7 5.5 L11 8.5 L7 11.5Z" fill="#3a8fc4"/></svg>Service goes here</li>
  <li><svg width="17" height="17" viewBox="0 0 17 17"><circle cx="8.5" cy="8.5" r="7.5" fill="#f2f2f2" stroke="#bbb"/><path d="M7 5.5 L11 8.5 L7 11.5Z" fill="#3a8fc4"/></svg>Service goes here</li>
  <li><svg width="17" height="17" viewBox="0 0 17 17"><circle cx="8.5" cy="8.5" r="7.5" fill="#f2f2f2" stroke="#bbb"/><path d="M7 5.5 L11 8.5 L7 11.5Z" fill="#3a8fc4"/></svg>Service goes here</li>
</ul>
<a class="abs btn-more" style="left:464px;top:917px">More</a>

<section class="abs clients">
  <h2 class="section-title" style="position:absolute;left:11px;top:8px"><b>Our</b> Clients</h2>
  <svg class="pager" style="left:528px" width="34" height="16" viewBox="0 0 34 16">
    <circle cx="8" cy="8" r="6.5" fill="#f2f2f2" stroke="#bbb"/><path d="M10 5 L6 8 L10 11Z" fill="#3a8fc4"/>
    <circle cx="26" cy="8" r="6.5" fill="#f2f2f2" stroke="#bbb"/><path d="M24 5 L28 8 L24 11Z" fill="#3a8fc4"/>
  </svg>
  <div class="rule"></div>
  <div class="client" style="left:10px"><div class="photo" role="img" aria-label="Client portrait photo"></div><span>Maplecrest Hospital</span></div>
  <div class="client" style="left:154px"><div class="photo" role="img" aria-label="Client portrait photo"></div><span>Maplecrest Hospital</span></div>
  <div class="client" style="left:298px"><div class="photo" role="img" aria-label="Client portrait photo"></div><span>Maplecrest Hospital</span></div>
  <div class="client" style="left:439px"><div class="photo" role="img" aria-label="Client portrait photo"></div><span>Maplecrest Hospital</span></div>
</section>

<footer class="abs site-footer">
  <div class="footer-contact">
    <strong>velorahelp</strong>
    Emergency Call : 1800-00-0417<br>
    Fax : 5550142938<br>
    E-mail : help4@velorahelp.example
  </div>
  <div class="find-us">Find Us : <i></i><i></i><i></i></div>
  <div class="legal">Copyright 2012 | Privacy Policy</div>
</footer>

</body>
</html>
```